Website Design for The Elder Nook

Please design and code a new website.
Here are the sites I like best:
http://www.voyaglint.com/alternate/
http://www.wheelgiftbay.org
Please make it similar but look at the competitor site (below) for images and wording. This is NOT a car donation site. It's a senior lead placement site like https://www.kinhavenfinder.com. I just like this sites above as a lead generation sites.
Competitor site:
https://www.kinhavenfinder.com (use ideas / verbiage from this site)
Updates
Competitor site:
Coding
Coded - Design and coding required
Number of Pages Required
1 page
Look and feel
Each slider illustrates characteristics of the customer's brand and the style your logo design should communicate.

```html
<!DOCTYPE html>
<html lang="en">
<head>
<meta charset="utf-8">
<title>The Elder Nook — Senior Living Advisors</title>
<link href="https://fonts.googleapis.com/css2?family=Montserrat:wght@400;600;700;800&family=Roboto:wght@400;500;700&display=swap" rel="stylesheet">
<style>
:root{
  --navy:#1c2a6e;
  --blue:#1f4fa5;
  --purple:#3b3593;
  --purple-deep:#2d2878;
  --green:#1d9f58;
  --green-dark:#15864a;
  --text:#333a44;
  --muted:#6b7280;
  --light:#f3f4f7;
  --line:#d7dae2;
  --white:#ffffff;
}
*{box-sizing:border-box;margin:0;padding:0}
html,body{width:1200px;height:5056px;overflow:hidden;background:var(--white)}
body{font-family:"Roboto",sans-serif;color:var(--text);position:relative}
h1,h2,h3,h4{font-family:"Montserrat",sans-serif}
.section{position:absolute;left:0;width:1200px}

/* header */
.site-header{top:0;height:118px;display:flex;align-items:center;justify-content:space-between;padding:0 40px}
.brand{display:flex;align-items:center;gap:14px}
.brand-dot{width:40px;height:40px;border-radius:50%;background:var(--green)}
.brand-name{font-family:"Montserrat",sans-serif;font-weight:700;font-size:30px;color:var(--navy)}
.brand-tag{font-size:11px;color:var(--muted);letter-spacing:1px;margin-top:2px}
.header-phone{display:flex;align-items:center;gap:14px}
.phone-ring{width:62px;height:62px;border-radius:50%;background:var(--navy);display:flex;align-items:center;justify-content:center}
.phone-num{font-family:"Montserrat",sans-serif;font-weight:800;font-size:32px;color:var(--navy)}
.phone-sub{font-size:13px;color:var(--muted)}

/* nav */
.main-nav{top:118px;height:46px;background:var(--navy);display:flex;align-items:center;padding-left:40px}
.main-nav a{color:var(--white);font-family:"Montserrat",sans-serif;font-weight:600;font-size:13px;text-decoration:none;margin-right:30px;text-transform:uppercase}
.nav-cta{position:absolute;right:0;top:0;width:410px;height:46px;background:var(--blue);color:var(--white);font-family:"Montserrat",sans-serif;font-weight:800;font-size:22px;display:flex;align-items:center;justify-content:center}

/* hero */
.hero{top:164px;height:746px}
.hero-photo{position:absolute;inset:0;background:linear-gradient(100deg,#cfd6de 0%,#e6eaee 35%,#aebccb 70%,#8797ab 100%)}
.lead-form{position:absolute;right:60px;top:0;width:350px;height:430px;background:rgba(255,255,255,.96);padding:18px 24px}
.field{height:32px;border-bottom:1px solid var(--line);font-size:13px;color:var(--text);display:flex;align-items:center;justify-content:space-between;margin-bottom:6px}
.field-row{display:flex;gap:14px}
.field-row .field{flex:1}
.field.msg{height:72px;align-items:flex-start;padding-top:8px}
.submit{margin-top:14px;width:120px;height:36px;background:var(--navy);color:var(--white);font-family:"Montserrat",sans-serif;font-weight:700;font-size:13px;display:flex;align-items:center;justify-content:center}
.support-band{position:absolute;left:0;top:492px;width:1200px;height:192px;display:flex}
.support-title{width:470px;background:var(--green);clip-path:polygon(0 0,100% 0,88% 100%,0 100%);padding:42px 40px;color:var(--white)}
.support-title h1{font-weight:800;font-size:34px;line-height:1.12;text-transform:uppercase}
.support-icons{flex:1;background:var(--white);display:flex;justify-content:space-around;align-items:center;padding:0 20px}
.s-icon{text-align:center;width:110px;font-size:12px;font-weight:700;color:var(--text);line-height:1.3}
.s-icon svg{display:block;margin:0 auto 10px}

/* how it works */
.how{top:940px;height:460px}
.sec-title{text-align:center;font-weight:700;font-size:30px;color:var(--navy)}
.sec-title span{color:var(--green)}
.steps{display:flex;gap:28px;padding:0 64px;margin-top:40px}
.step{width:255px}
.step h4{font-size:13px;font-weight:700;color:var(--text);margin-bottom:12px}
.step-photo{height:150px;margin-bottom:14px}
.step p{font-size:13px;line-height:1.5;color:var(--text)}

/* no cost */
.no-cost{top:1466px;height:372px;background:var(--purple)}
.no-cost-photo{position:absolute;left:0;top:0;width:700px;height:372px;background:linear-gradient(90deg,#c8b9a6 0%,#9c8d8d 55%,var(--purple) 100%)}
.no-cost-copy{position:absolute;left:700px;top:110px;color:var(--white)}
.no-cost-copy h2{font-size:34px;font-weight:700}
.no-cost-copy p{font-size:17px;margin-top:6px;line-height:1.4;width:430px}
.no-cost-copy .call{font-family:"Montserrat",sans-serif;font-weight:700;font-size:34px;margin-top:26px}

/* veterans */
.veteran{top:1886px;height:380px}
.veteran h2{position:absolute;left:96px;top:90px;font-size:28px;font-weight:700;color:var(--navy)}
.veteran h2 span{color:var(--green)}
.veteran p{position:absolute;left:96px;top:152px;width:560px;font-size:17px;line-height:1.55}
.btn-green{position:absolute;left:96px;top:290px;width:210px;height:44px;background:var(--green);color:var(--white);font-family:"Montserrat",sans-serif;font-weight:600;font-size:15px;display:flex;align-items:center;justify-content:center}
.vet-photo{position:absolute;left:830px;top:70px;width:265px;height:265px;border-radius:50%;background:radial-gradient(circle at 40% 40%,#e9ecf2,#9aa7bd 70%,#6a7690);border:6px solid var(--light)}

/* testimonials */
.testimonials{top:2325px;height:460px;background:linear-gradient(90deg,var(--purple-deep),var(--purple))}
.testimonials h2{text-align:center;color:var(--white);font-size:30px;font-weight:700;margin-top:60px}
.t-row{display:flex;gap:40px;padding:0 84px;margin-top:48px}
.t-card{width:317px;position:relative;color:var(--white)}
.t-quote{font-size:14px;line-height:1.5;padding-left:28px}
.qmark{position:absolute;font-family:"Montserrat",sans-serif;font-weight:800;font-size:54px;color:var(--green);line-height:1}
.t-foot{display:flex;justify-content:space-between;align-items:center;margin-top:22px}
.t-name{font-style:italic;font-weight:700;font-size:15px}
.t-avatar{width:72px;height:72px;border-radius:50%;background:#c7cad8;border:4px solid var(--white)}
.dots{display:flex;justify-content:center;gap:8px;margin-top:36px}
.dots i{width:10px;height:10px;border-radius:50%;border:2px solid var(--white)}
.dots i.on{background:var(--white)}

/* states */
.states{top:2930px;height:460px}
.state-wrap{display:flex;padding:0 92px;margin-top:44px;gap:60px}
.care-tabs{width:230px}
.tab{display:flex;align-items:center;height:48px;margin-bottom:10px;border:1px solid var(--line);font-weight:500;font-size:16px}
.tab .tab-icon{width:44px;height:46px;background:var(--blue);display:flex;align-items:center;justify-content:center;margin-right:16px}
.tab.active{color:var(--green)}
.tab.active .tab-icon{background:var(--green)}
.state-cols{display:flex;gap:46px;flex:1}
.state-cols ul{list-style:none;width:150px;font-size:14.5px;line-height:1.55}

/* advisor */
.advisor{top:3490px;height:440px;background:linear-gradient(90deg,var(--purple-deep),var(--purple))}
.advisor-photo{position:absolute;right:0;top:0;width:560px;height:440px;background:linear-gradient(90deg,var(--purple) 0%,#b7aea4 35%,#ddd6cc 100%)}
.advisor-copy{position:absolute;left:80px;top:90px;color:var(--white)}
.advisor-copy h2{font-size:34px;font-weight:700;line-height:1.2}
.advisor-copy p{font-size:16px;margin-top:14px;width:440px;line-height:1.45}
.perks{list-style:none;margin-top:20px}
.perks li{display:flex;align-items:center;gap:14px;font-weight:500;font-size:16px;margin-bottom:14px}

/* city lists */
.city-lists{top:3990px;height:560px;display:flex;padding:0 92px;gap:60px}
.city-col{width:300px}
.city-col h3{font-size:19px;font-weight:700;color:var(--navy);margin-bottom:14px}
.city-col h3 span{color:var(--green)}
.city-col ul{list-style:none;font-size:14px;line-height:1.6}

/* footer */
.site-footer{top:4580px;height:410px;border-top:1px solid var(--line)}
.f-col{position:absolute;top:80px}
.f-col h4{font-size:13px;font-weight:700;color:var(--navy);text-transform:uppercase;margin-bottom:14px}
.f-col p,.f-col li{font-size:13px;line-height:1.55;color:var(--muted)}
.f-col ul{list-style:none}
.socials{display:flex;gap:8px}
.socials i{width:32px;height:32px;background:var(--blue);border-radius:4px}
.f-brand{position:absolute;right:0;top:0;width:360px;height:410px;background:var(--green);clip-path:polygon(14% 0,100% 0,100% 100%,0 100%);padding:70px 0 0 80px;color:var(--white)}
.f-brand .brand-name{color:var(--white);font-size:28px}
.f-brand .brand-dot{background:var(--white)}
.f-phone{display:flex;align-items:center;gap:12px;margin-top:60px}
.f-phone .phone-ring{width:52px;height:52px;background:var(--white)}
.f-phone .num{font-family:"Montserrat",sans-serif;font-weight:800;font-size:26px}
.f-phone .sub{font-size:12px}
.copyright{top:4990px;height:66px;background:var(--light);display:flex;align-items:center;justify-content:center;font-size:12px;font-weight:500;color:var(--text)}
</style>
</head>
<body>

<header class="section site-header">
  <div class="brand">
    <div class="brand-dot"></div>
    <div>
      <div class="brand-name">The Elder Nook</div>
      <div class="brand-tag">CONNECTING FAMILIES TO SENIOR LIVING</div>
    </div>
  </div>
  <div class="header-phone">
    <div class="phone-ring">
      <svg width="28" height="28" viewBox="0 0 24 24"><path fill="#fff" d="M6.6 10.8a15 15 0 0 0 6.6 6.6l2.2-2.2a1 1 0 0 1 1-.25 11.4 11.4 0 0 0 3.6.57 1 1 0 0 1 1 1V20a1 1 0 0 1-1 1A17 17 0 0 1 3 4a1 1 0 0 1 1-1h3.5a1 1 0 0 1 1 1c0 1.25.2 2.45.57 3.6a1 1 0 0 1-.25 1z"/></svg>
    </div>
    <div>
      <div class="phone-num">1-800-555-0142</div>
      <div class="phone-sub">Talk Today to a Local Advisor for FREE</div>
    </div>
  </div>
</header>

<nav class="section main-nav">
  <a>Assisted Living</a><a>Memory Care</a><a>Nursing Homes</a><a>More Living Options ▾</a><a>Planning &amp; Advice</a>
  <div class="nav-cta">CONTACT US NOW!</div>
</nav>

<section class="section hero">
  <div class="hero-photo" role="img" aria-label="Smiling senior man in a cardigan standing outdoors"></div>
  <form class="lead-form">
    <div class="field">Name*</div>
    <div class="field">Email Address*</div>
    <div class="field">Contact Number*</div>
    <div class="field">Interested In <span>▾</span></div>
    <div class="field">City*</div>
    <div class="field-row"><div class="field">State* <span>▾</span></div><div class="field">Zip Code*</div></div>
    <div class="field msg">Message</div>
    <div class="submit">SUBMIT</div>
  </form>
  <div class="support-band">
    <div class="support-title"><h1>The support you<br>need to make the<br>right choice</h1></div>
    <div class="support-icons">
      <div class="s-icon"><svg width="48" height="48" viewBox="0 0 48 48" fill="none" stroke="#1c2a6e" stroke-width="3"><circle cx="24" cy="16" r="9"/><path d="M8 44c0-9 7-15 16-15s16 6 16 15"/></svg>Dedicated local advisor</div>
      <div class="s-icon"><svg width="48" height="48" viewBox="0 0 48 48" fill="none" stroke="#1c2a6e" stroke-width="3"><path d="M6 22 24 8l18 14v20H6z"/><rect x="19" y="28" width="10" height="14"/></svg>Hand-picked list of communities to match your needs</div>
      <div class="s-icon"><svg width="48" height="48" viewBox="0 0 48 48" fill="none" stroke="#1c2a6e" stroke-width="3"><rect x="10" y="6" width="28" height="36" rx="2"/><path d="M17 16h14M17 24h14M17 32h8"/></svg>Full details and pricing</div>
      <div class="s-icon"><svg width="48" height="48" viewBox="0 0 48 48" fill="none" stroke="#1c2a6e" stroke-width="3"><rect x="6" y="10" width="36" height="32" rx="2"/><path d="M6 20h36M15 5v9M33 5v9"/></svg>Help scheduling tours</div>
      <div class="s-icon"><svg width="48" height="48" viewBox="0 0 48 48" fill="none" stroke="#1c2a6e" stroke-width="3"><path d="M4 26l10-8 8 4 8-4 14 8M14 18l10 14M34 22 24 32"/></svg>More in support</div>
    </div>
  </div>
</section>

<section class="section how">
  <h2 class="sec-title">How our <span>service works</span></h2>
  <div class="steps">
    <div class="step">
      <h4>01. Talk with your local advisor</h4>
      <div class="step-photo" role="img" aria-label="Advisor wearing a headset on a call" style="background:linear-gradient(135deg,#e9e2d8,#b9a48c)"></div>
      <p>Call us to get connected to your local Senior Living Advisor, who will do an assessment of you or your loved one's lifestyle, care needs, budget, and preferences for senior living.</p>
    </div>
    <div class="step">
      <h4>02. Get information on care options</h4>
      <div class="step-photo" role="img" aria-label="Family reviewing care options on a laptop" style="background:linear-gradient(135deg,#d9cbb8,#8d7b68)"></div>
      <p>Based on your assessment, your Advisor will send you information on senior living communities tailored to your needs, saving you the time trying to find the right ones to evaluate.</p>
    </div>
    <div class="step">
      <h4>03. Choose communities to visit</h4>
      <div class="step-photo" role="img" aria-label="Seniors touring a community common room" style="background:linear-gradient(135deg,#cfd8cf,#8a9a86)"></div>
      <p>Have tours scheduled for you, get tips on looking for the right fit for your needs, and consult with your Advisor at any time - all at no cost to you.</p>
    </div>
    <div class="step">
      <h4>04. Transition to new home</h4>
      <div class="step-photo" role="img" aria-label="Senior couple settling into a new home" style="background:linear-gradient(135deg,#e3dccf,#a89b86)"></div>
      <p>When you've selected the right living arrangement, get guidance on making the move as smooth as possible.</p>
    </div>
  </div>
</section>

<section class="section no-cost">
  <div class="no-cost-photo" role="img" aria-label="Happy senior couple smiling together"></div>
  <div class="no-cost-copy">
    <h2>There's No Cost to You</h2>
    <p>We work with over 20,000 senior living communities. Our community partners pay us for placement services.</p>
    <div class="call">Call 800-555-0142</div>
  </div>
</section>

<section class="section veteran">
  <h2>Access up to $2,000 per month <span>in veteran's aid</span></h2>
  <p>We work with Veterans every day. Most veteran families do not know of a key benefit available to them and their families. It's called the Veteran's Aid and Attendance benefit. This benefit can help pay for senior living and home care.</p>
  <div class="btn-green">Learn More</div>
  <div class="vet-photo" role="img" aria-label="Veteran saluting in front of a flag"></div>
</section>

<section class="section testimonials">
  <h2>97% of our customers recommend our service</h2>
  <div class="t-row">
    <div class="t-card">
      <span class="qmark" style="left:0;top:-8px">“</span>
      <p class="t-quote">Lorem ipsum dolor sit amet, con sectetuer adipiscing elit, sed diam nonummy nibh euismod tincidunt ut laoreet dolor magna aliquam erat volu.</p>
      <div class="t-foot"><span class="t-name">Marla Benton</span><div class="t-avatar" role="img" aria-label="Customer portrait"></div></div>
    </div>
    <div class="t-card">
      <span class="qmark" style="left:0;top:-8px">“</span>
      <p class="t-quote">Lorem ipsum dolor sit amet, con sectetuer adipiscing elit, sed diam nonummy nibh euismod tincidunt ut laoreet dolor magna aliquam erat volu.</p>
      <div class="t-foot"><span class="t-name">Ruth Ellery</span><div class="t-avatar" role="img" aria-label="Customer portrait"></div></div>
    </div>
    <div class="t-card">
      <span class="qmark" style="left:0;top:-8px">“</span>
      <p class="t-quote">Lorem ipsum dolor sit amet, con sectetuer adipiscing elit, sed diam nonummy nibh euismod tincidunt ut laoreet dolor magna aliquam erat volu.</p>
      <div class="t-foot"><span class="t-name">Owen Pritchard</span><div class="t-avatar" role="img" aria-label="Customer portrait"></div></div>
    </div>
  </div>
  <div class="dots"><i class="on"></i><i></i><i></i><i></i></div>
</section>

<section class="section states">
  <h2 class="sec-title">Senior living <span>by state</span></h2>
  <div class="state-wrap">
    <div class="care-tabs">
      <div class="tab active"><span class="tab-icon"><svg width="22" height="22" viewBox="0 0 24 24" fill="#fff"><circle cx="8" cy="5" r="3"/><circle cx="16" cy="5" r="3"/><rect x="5" y="9" width="6" height="13"/><rect x="13" y="9" width="6" height="13"/></svg></span>Assisted Living<span style="margin-left:auto;margin-right:12px">◂</span></div>
      <div class="tab"><span class="tab-icon"><svg width="22" height="22" viewBox="0 0 24 24" fill="none" stroke="#fff" stroke-width="2"><circle cx="11" cy="11" r="7"/><path d="M16 16l5 5"/></svg></span>Memory Care</div>
      <div class="tab"><span class="tab-icon"><svg width="22" height="22" viewBox="0 0 24 24" fill="#fff"><circle cx="12" cy="6" r="4"/><path d="M4 22c0-5 4-8 8-8s8 3 8 8z"/></svg></span>Independent Living</div>
      <div class="tab"><span class="tab-icon"><svg width="22" height="22" viewBox="0 0 24 24" fill="#fff"><path d="M9 3h6v6h6v6h-6v6H9v-6H3V9h6z"/></svg></span>Nursing Home</div>
      <div class="tab"><span class="tab-icon"><svg width="22" height="22" viewBox="0 0 24 24" fill="#fff"><path d="M2 12 12 3l10 9h-3v9H5v-9z"/></svg></span>Care Homes</div>
    </div>
    <div class="state-cols">
      <ul><li>Alabama</li><li>Arizona</li><li>Arkansas</li><li>California</li><li>Colorado</li><li>Connecticut</li><li>Delaware</li><li>District of Columbia</li><li>Florida</li><li>Georgia</li><li>Hawaii</li><li>Idaho</li><li>Illinois</li><li>Indiana</li><li>Iowa</li><li>Kansas</li><li>Kentucky</li></ul>
      <ul><li>Louisiana</li><li>Maine</li><li>Maryland</li><li>Massachusetts</li><li>Michigan</li><li>Minnesota</li><li>Mississippi</li><li>Missouri</li><li>Montana</li><li>Nebraska</li><li>Nevada</li><li>New Hampshire</li><li>New Jersey</li><li>New Mexico</li><li>New York</li><li>North Carolina</li><li>North Dakota</li></ul>
      <ul><li>Ohio</li><li>Oklahoma</li><li>Oregon</li><li>Pennsylvania</li><li>Rhode Island</li><li>South Carolina</li><li>South Dakota</li><li>Tennessee</li><li>Texas</li><li>Utah</li><li>Vermont</li><li>Virginia</li><li>Washington</li><li>West Virginia</li><li>Wisconsin</li><li>Wyoming</li></ul>
    </div>
  </div>
</section>

<section class="section advisor">
  <div class="advisor-photo" role="img" aria-label="Advisor sitting with a senior woman at home"></div>
  <div class="advisor-copy">
    <h2>Your local advisor.<br>You decide.</h2>
    <p>Over 400 senior advisors across the U.S. and Canada are ready to help your family with:</p>
    <ul class="perks">
      <li><svg width="26" height="26" viewBox="0 0 24 24" fill="none" stroke="#fff" stroke-width="2"><path d="M12 22s7-7 7-12a7 7 0 0 0-14 0c0 5 7 12 7 12z"/><circle cx="12" cy="10" r="2.5"/></svg>Insider's tips for the area near you</li>
      <li><svg width="26" height="26" viewBox="0 0 24 24" fill="none" stroke="#fff" stroke-width="2"><path d="M4 12l5 5L20 6"/></svg>Advice tailored to your unique situation</li>
      <li><svg width="26" height="26" viewBox="0 0 24 24" fill="none" stroke="#fff" stroke-width="2"><circle cx="12" cy="12" r="9"/><path d="M12 7v5l3 3"/></svg>Time saving know-how and resources</li>
    </ul>
  </div>
</section>

<section class="section city-lists">
  <div class="city-col">
    <h3>Independent <span>living</span></h3>
    <ul><li>New York Independent Living</li><li>Los Angeles Independent Living</li><li>Chicago Independent Living</li><li>Dallas Independent Living</li><li>Houston Independent Living</li><li>Washington DC Independent Living</li><li>Philadelphia Independent Living</li><li>Miami Independent Living</li><li>Atlanta Independent Living</li><li>Boston Independent Living</li><li>San Francisco Independent Living</li><li>Phoenix Independent Living</li><li>Orange County Independent Living</li><li>Detroit Independent Living</li><li>Seattle Independent Living</li><li>Minneapolis Independent Living</li><li>San Diego Independent Living</li><li>Tampa Independent Living</li><li>Denver Independent Living</li><li>St. Louis Independent Living</li><li>Baltimore Independent Living</li></ul>
  </div>
  <div class="city-col">
    <h3>Memory <span>care</span></h3>
    <ul><li>New York Memory Care</li><li>Los Angeles Memory Care</li><li>Chicago Memory Care</li><li>Dallas Memory Care</li><li>Houston Memory Care</li><li>Washington DC Memory Care</li><li>Philadelphia Memory Care</li><li>Miami Memory Care</li><li>Atlanta Memory Care</li><li>Boston Memory Care</li><li>San Francisco Memory Care</li><li>Phoenix Memory Care</li><li>Orange County Memory Care</li><li>Detroit Memory Care</li><li>Seattle Memory Care</li><li>Minneapolis Memory Care</li><li>San Diego Memory Care</li><li>Tampa Memory Care</li><li>Denver Memory Care</li><li>St. Louis Memory Care</li><li>Baltimore Memory Care</li></ul>
  </div>
  <div class="city-col">
    <h3>Nursing <span>homes</span></h3>
    <ul><li>New York Nursing Homes</li><li>Los Angeles Nursing Homes</li><li>Chicago Nursing Homes</li><li>Dallas Nursing Homes</li><li>Houston Nursing Homes</li><li>Washington DC Nursing Homes</li><li>Philadelphia Nursing Homes</li><li>Miami Nursing Homes</li><li>Atlanta Nursing Homes</li><li>Boston Nursing Homes</li><li>San Francisco Nursing Homes</li><li>Phoenix Nursing Homes</li><li>Orange County Nursing Homes</li><li>Detroit Nursing Homes</li><li>Seattle Nursing Homes</li><li>Minneapolis Nursing Homes</li><li>San Diego Nursing Homes</li><li>Tampa Nursing Homes</li><li>Denver Nursing Homes</li><li>St. Louis Nursing Homes</li><li>Baltimore Nursing Homes</li></ul>
  </div>
</section>

<footer class="section site-footer">
  <div class="f-col" style="left:60px;width:280px">
    <h4>About The Elder Nook</h4>
    <p>Lorem ipsum dolor sit amet, consectetuer adipiscing elit, sed diam nonummy nibh euismod tincidunt ut laoreet dolore magna aliquam erat volutpat. Ut wisi enim ad minim veniam, quis nostrud exerci tation ullamcorper suscipit lobortis nisl ut.</p>
  </div>
  <div class="f-col" style="left:390px">
    <h4>Quick Links</h4>
    <ul><li>Assisted Living</li><li>Memory Care</li><li>Nursing Home</li><li>More Living Options</li><li>Planning &amp; Advice</li><li>How Our Service Works</li></ul>
  </div>
  <div class="f-col" style="left:590px">
    <h4>Follow</h4>
    <div class="socials"><i></i><i></i><i></i></div>
  </div>
  <div class="f-brand">
    <div class="brand"><div class="brand-dot"></div><div class="brand-name">The Elder Nook</div></div>
    <div class="f-phone">
      <div class="phone-ring"><svg width="24" height="24" viewBox="0 0 24 24"><path fill="#1d9f58" d="M6.6 10.8a15 15 0 0 0 6.6 6.6l2.2-2.2a1 1 0 0 1 1-.25 11.4 11.4 0 0 0 3.6.57 1 1 0 0 1 1 1V20a1 1 0 0 1-1 1A17 17 0 0 1 3 4a1 1 0 0 1 1-1h3.5a1 1 0 0 1 1 1c0 1.25.2 2.45.57 3.6a1 1 0 0 1-.25 1z"/></svg></div>
      <div><div class="num">1-800-555-0142</div><div class="sub">Talk Today to a Local Advisor for FREE</div></div>
    </div>
  </div>
</footer>

<div class="section copyright">COPYRIGHT © 2018 THE ELDER NOOK. ALL RIGHTS RESERVED.</div>

</body>
</html>
```